Business card

I have changed logo's and colors. I have uploaded the new logo and colors.

In my head I am thinking about the main logo and text beside logo to be on one side of the card. The other side of the card to have just my picture and contact information.

The "R" emblem and the "equal housing" emblem... cut he MLS from the "R". and remove the wording from the house emblem.

Info on Card:

Lyle Penrose
Designated Broker, CDPE, CNE, GRI
Direct: 602.555.0143
Fax: 623.555.0187
Lyle@PenroseandAssociates.example
www.PenroseandAssociates.example
4153 West Marlow Lane Glendale, AZ 85391

Please see brief as I have uploaded a new logo and a few notes.

Reason: I changed the logo and colors. Please see brief

I am leaning towards maybe a black business card(or at least on the front where the logo is). I liked several designs that were submitted. Please re-submit.

```html
<!DOCTYPE html>
<html lang="en">
<head>
<meta charset="utf-8">
<title>Penrose &amp; Associates – Business Card</title>
<link rel="stylesheet" href="https://fonts.googleapis.com/css2?family=Arimo:wght@400;700&display=swap">
<style>
  :root {
    --bg: #d9d9d9;
    --card: #ffffff;
    --orange: #e8672a;
    --teal: #7fa9ae;
    --ink: #2b2b2b;
    --muted: #9aa5a8;
    --badge: #b9c6cc;
    --photo-a: #e7eaee;
    --photo-b: #8b9099;
  }
  * { box-sizing: border-box; margin: 0; padding: 0; }
  html, body { width: 1200px; height: 864px; overflow: hidden; }
  body {
    background: var(--bg);
    font-family: "Arimo", Arial, sans-serif;
    color: var(--ink);
    position: relative;
  }
  .card {
    position: absolute;
    left: 260px;
    width: 680px;
    height: 389px;
    background: var(--card);
    box-shadow: 0 2px 8px rgba(0,0,0,0.15);
    overflow: hidden;
  }
  .card--front { top: 28px; }
  .card--back { top: 447px; }

  /* Front */
  .brand {
    position: absolute;
    left: 48px;
    top: 150px;
    display: flex;
    align-items: center;
    gap: 18px;
  }
  .brand__dot {
    width: 64px; height: 64px;
    border-radius: 50%;
    background: var(--orange);
  }
  .brand__name {
    font-size: 34px;
    font-weight: 400;
    letter-spacing: 4px;
    color: var(--teal);
    line-height: 1.2;
  }
  .agent {
    position: absolute;
    right: 48px;
    top: 150px;
    text-align: right;
  }
  .agent__name {
    color: var(--orange);
    font-size: 22px;
    font-weight: 700;
    letter-spacing: 1px;
    text-transform: uppercase;
  }
  .agent__title { font-size: 14px; margin-top: 6px; }
  .agent__creds { font-size: 14px; margin-top: 2px; }
  .phones {
    position: absolute;
    right: 48px;
    bottom: 44px;
    list-style: none;
  }
  .phones li, .contact li {
    display: flex;
    align-items: center;
    justify-content: flex-end;
    gap: 12px;
    font-size: 16px;
    line-height: 26px;
  }
  .icon { width: 16px; height: 16px; fill: var(--orange); flex: none; }

  /* Back */
  .portrait {
    position: absolute;
    left: 60px;
    top: 0;
    width: 240px;
    height: 389px;
    background: linear-gradient(180deg, var(--photo-a) 0%, var(--photo-b) 100%);
  }
  .notes {
    position: absolute;
    left: 350px;
    right: 40px;
    top: 50px;
  }
  .notes__line {
    border-bottom: 2px dotted var(--ink);
    height: 28px;
  }
  .badges {
    position: absolute;
    left: 420px;
    top: 196px;
    display: flex;
    align-items: flex-end;
    gap: 30px;
  }
  .badge-house { width: 44px; height: 40px; fill: var(--ink); }
  .badge-listing { width: 60px; height: 30px; background: var(--badge); margin-top: 20px; }
  .contact {
    position: absolute;
    right: 40px;
    bottom: 30px;
    list-style: none;
    text-align: right;
  }
  .contact li { font-size: 15px; }
</style>
</head>
<body>

<section class="card card--front" aria-label="Card front">
  <div class="brand">
    <span class="brand__dot"></span>
    <span class="brand__name">PENROSE<br>&amp; ASSOCIATES</span>
  </div>

  <div class="agent">
    <p class="agent__name">Lyle Penrose</p>
    <p class="agent__title">Designated Broker</p>
    <p class="agent__creds">CDPE, CNE, GRI</p>
  </div>

  <ul class="phones">
    <li>602.555.0143
      <svg class="icon" viewBox="0 0 16 16" aria-hidden="true"><circle cx="8" cy="4.5" r="3.5"/><path d="M1 16c0-4 3-6.5 7-6.5s7 2.5 7 6.5z"/></svg>
    </li>
    <li>623.555.0187
      <svg class="icon" viewBox="0 0 16 16" aria-hidden="true"><rect x="4" y="1" width="8" height="4"/><rect x="1" y="6" width="14" height="6" rx="1"/><rect x="4" y="10" width="8" height="5"/></svg>
    </li>
  </ul>
</section>

<section class="card card--back" aria-label="Card back">
  <div class="portrait" role="img" aria-label="Portrait photo of the broker in a dark blazer"></div>

  <div class="notes">
    <div class="notes__line"></div>
    <div class="notes__line"></div>
    <div class="notes__line"></div>
    <div class="notes__line"></div>
  </div>

  <div class="badges">
    <svg class="badge-house" viewBox="0 0 44 40" role="img" aria-label="Housing badge"><path d="M22 0 44 16h-5v24H5V16H0z"/></svg>
    <div class="badge-listing" role="img" aria-label="Listing service badge"></div>
  </div>

  <ul class="contact">
    <li>Lyle@PenroseandAssociates.example
      <svg class="icon" viewBox="0 0 16 16" aria-hidden="true"><rect x="1" y="3" width="14" height="10"/><path d="M1 3l7 6 7-6" fill="none" stroke="#fff" stroke-width="1.4"/></svg>
    </li>
    <li>www.PenroseandAssociates.example
      <svg class="icon" viewBox="0 0 16 16" aria-hidden="true"><circle cx="8" cy="8" r="7"/><path d="M1 8h14M8 1c3 3 3 11 0 14M8 1c-3 3-3 11 0 14" fill="none" stroke="#fff" stroke-width="1"/></svg>
    </li>
    <li>4153 West Marlow Lane Glendale, AZ 85391
      <svg class="icon" viewBox="0 0 16 16" aria-hidden="true"><path d="M8 0C4.7 0 2 2.6 2 5.8 2 10 8 16 8 16s6-6 6-10.2C14 2.6 11.3 0 8 0zm0 8.3A2.5 2.5 0 1 1 8 3.3a2.5 2.5 0 0 1 0 5z"/></svg>
    </li>
  </ul>
</section>

</body>
</html>
```